Transform Your Giving

I need a tri-fold brochure that will fit in a standard number 10 business envelope. Meadowlark and Allied Services is a charitable nonprofit. The goal of this brochure is to stimulate people into thinking about other ways to make a donation. The design should communicate the essential information on donation options, create a sense of professional integrity, be graphically sharp, easy to read and laid out in a way that doesn't make the material appear crowded.

```html
<!DOCTYPE html>
<html lang="en">
<head>
<meta charset="utf-8">
<title>Transform Your Giving – Tri-fold Brochure</title>
<link rel="stylesheet" href="https://fonts.googleapis.com/css2?family=Montserrat:wght@400;500;600;700;800;900&display=swap">
<style>
:root{
  --navy:#2b2a72;
  --green:#4cb748;
  --green-dark:#3fa83c;
  --stage:#9a9a9a;
  --paper:#ffffff;
  --inside:#eeedf1;
  --inside-mid:#e4e3e8;
  --ink:#3a3a44;
}
*{margin:0;padding:0;box-sizing:border-box}
html,body{width:1200px;height:1200px;overflow:hidden;background:var(--stage);font-family:'Montserrat',sans-serif;color:var(--ink)}
.abs{position:absolute}
.sheet{position:absolute;overflow:hidden}
.sheet--outside{left:251px;top:60px;width:672px;height:523px;background:var(--paper)}
.sheet--inside{left:251px;top:616px;width:675px;height:525px;background:var(--inside)}
.panel{position:absolute;top:0;height:100%;overflow:hidden}

/* outside panel 1 */
.impact{left:0;width:224px;background:var(--paper)}
.impact__title{top:20px;left:0;width:224px;text-align:center;font-weight:800;font-size:15.5px;line-height:18px;color:var(--navy)}
.impact__title span{color:var(--green)}
.impact__text{top:66px;left:20px;width:184px;text-align:center;font-size:7.6px;line-height:9.9px;color:var(--ink)}
.checklist{top:159px;left:45px;width:134px}
.checklist li{list-style:none;height:16px;margin-bottom:5.6px;border:1px solid var(--green);display:flex;align-items:center;justify-content:center;gap:4px;font-size:8.6px;color:var(--ink)}
.photo-couple{left:0;top:318px;width:224px;height:205px}

/* outside panel 2 */
.contact{left:224px;width:224px;background:var(--green);color:#fff;text-align:center}
.brand{left:0;width:100%;text-align:center;font-weight:800;color:#fff}
.brand__name{font-size:28px;line-height:30px;letter-spacing:1px}
.brand__sub{font-size:4.6px;letter-spacing:.3px;margin-top:2px}
.contact__intro{top:90px;left:14px;width:196px;font-size:9.1px;line-height:11.3px;font-weight:500}
.quote{top:194px;left:34px;width:160px;height:48px;border:1px solid #fff;border-radius:7px;padding-top:9px}
.quote__mark{top:182px;left:100px;width:24px;height:16px;background:var(--green)}
.quote p{font-style:italic;font-size:6.8px;line-height:10px}
.quote b{font-size:7px;display:block;margin-top:3px}
.will{top:251px;left:0;width:224px;line-height:11px}
.will__a{font-size:8px;font-weight:500}
.will__b{font-size:12.6px;font-weight:800;line-height:16px}
.will__c{font-size:8px;color:#e6f4e4}
.will__d{font-size:9px;font-weight:800}
.pill-navy{top:322px;left:61px;width:99px;height:17px;border-radius:9px;background:var(--navy);font-size:10.5px;font-weight:800;line-height:17px}
.question{top:345px;left:0;width:224px}
.question h3{font-size:11px;font-weight:800;line-height:13px}
.question p{font-size:8.2px;line-height:10px;font-weight:500}
.rows{top:386px;left:57px;width:160px;text-align:left}
.row{display:flex;align-items:center;gap:6px;height:20px;margin-bottom:4.5px;font-size:6.4px;line-height:8px}
.row svg{flex:none}
.follow{top:460px;left:60px;font-size:8px;font-weight:600;display:flex;align-items:center;gap:3px}
.dot{width:11px;height:11px;border-radius:50%;display:inline-block}
.disclaimer{top:485px;left:20px;width:184px;font-size:3.6px;line-height:4.8px}

/* outside panel 3 */
.cover{left:448px;width:224px;background:var(--paper)}
.cover__title{top:222px;left:0;width:224px;text-align:center;font-weight:900;color:#fff;font-size:17px;line-height:20px}
.cover__title span{display:block;color:var(--green);font-size:24.5px;line-height:26px}
.cover__tag{top:272px;left:20px;width:184px;height:21px;border-top:1px solid #8c8bb8;border-bottom:1px solid #8c8bb8;display:flex;align-items:center;justify-content:center;gap:5px;color:#fff;font-weight:800;font-size:11px}
.cover__lead{top:302px;left:0;width:224px;text-align:center;color:#fff;font-weight:700;font-size:7.6px;line-height:10px}
.cover__icons{top:335px;left:8px;width:210px;display:flex;justify-content:space-between;color:#fff}
.ico{width:40px;text-align:center;font-size:5px;font-weight:700;line-height:6px}
.ico svg{display:block;margin:0 auto 4px}
.cover__brand{top:443px}
.cover__brand .brand__name{color:var(--navy);font-size:34px;line-height:36px}
.cover__brand .brand__sub{color:var(--navy);font-size:5.4px}

/* inside */
.hero{left:0;top:0;width:675px;height:170px}
.bubble{left:23px;top:42px;width:229px;height:80px;background:var(--navy);border-radius:40px;border:2px solid #fff}
.bubble__num{left:26px;top:-2px;font-size:74px;font-weight:800;color:var(--green);line-height:80px}
.bubble__text{left:68px;top:9px;font-size:19.5px;line-height:19px;font-weight:800;color:#fff}
.way{position:absolute}
.way__icon{position:absolute;width:66px;height:66px;border-radius:50%;background:var(--navy);display:flex;align-items:center;justify-content:center}
.way__title{position:absolute;font-weight:700;color:var(--navy);font-size:10.8px;line-height:13.3px}
.way__hint{position:absolute;font-weight:700;color:var(--green);font-size:5.5px;line-height:7px}
.way__body{position:absolute;font-size:5.5px;line-height:7.3px;color:var(--ink)}
.how{position:absolute;height:10px;padding:0 5px;border-radius:3px;background:var(--green);color:#fff;font-size:6px;font-weight:600;line-height:10px}
.tick{display:flex;gap:6px;align-items:flex-start}
.tick svg{flex:none;margin-top:1px}
.inside-mid{left:222px;top:0;width:222px;height:525px;background:linear-gradient(90deg,var(--inside-mid),var(--inside) 20%,var(--inside) 80%,var(--inside-mid))}
.inside-brand{left:222px;top:418px;width:222px;height:107px}
.inside-brand .brand{top:38px}
.inside-brand .brand__name{color:var(--navy);font-size:32px;line-height:34px}
.inside-brand .brand__sub{color:var(--navy);font-size:5px}
</style>
</head>
<body>

<!-- OUTSIDE -->
<section class="sheet sheet--outside">

  <div class="panel impact">
    <h2 class="abs impact__title">THE IMPACT OF<br><span>YOUR GIFT</span></h2>
    <p class="abs impact__text">Your generosity drives our mission. With every Smart gift you're supporting Meadowlark and Allied Services. Join our community of Smart Givers today and make an enduring impact. With Smart Giving your generosity reaches further. Begin your Smart Giving journey with us today.</p>
    <ul class="abs checklist">
      <li><svg width="8" height="8" viewBox="0 0 10 10"><circle cx="5" cy="5" r="4.2" fill="none" stroke="#4cb748" stroke-width="1"/><path d="M3 5l1.5 1.5L7.3 3.6" fill="none" stroke="#4cb748" stroke-width="1"/></svg>Stocks and Securities</li>
      <li><svg width="8" height="8" viewBox="0 0 10 10"><circle cx="5" cy="5" r="4.2" fill="none" stroke="#4cb748" stroke-width="1"/><path d="M3 5l1.5 1.5L7.3 3.6" fill="none" stroke="#4cb748" stroke-width="1"/></svg>DAFs</li>
      <li><svg width="8" height="8" viewBox="0 0 10 10"><circle cx="5" cy="5" r="4.2" fill="none" stroke="#4cb748" stroke-width="1"/><path d="M3 5l1.5 1.5L7.3 3.6" fill="none" stroke="#4cb748" stroke-width="1"/></svg>QCDs</li>
      <li><svg width="8" height="8" viewBox="0 0 10 10"><circle cx="5" cy="5" r="4.2" fill="none" stroke="#4cb748" stroke-width="1"/><path d="M3 5l1.5 1.5L7.3 3.6" fill="none" stroke="#4cb748" stroke-width="1"/></svg>Crypto</li>
      <li><svg width="8" height="8" viewBox="0 0 10 10"><circle cx="5" cy="5" r="4.2" fill="none" stroke="#4cb748" stroke-width="1"/><path d="M3 5l1.5 1.5L7.3 3.6" fill="none" stroke="#4cb748" stroke-width="1"/></svg>Charitable Annuity</li>
    </ul>
    <svg class="abs" style="left:0;top:300px" width="224" height="223" viewBox="0 0 224 223">
      <defs><linearGradient id="gardenTone" x1="0" y1="0" x2="1" y2="1"><stop offset="0" stop-color="#7d9a62"/><stop offset=".5" stop-color="#a86a86"/><stop offset="1" stop-color="#5d6b45"/></linearGradient></defs>
      <path d="M0 30 Q112 -15 224 30 L224 223 L0 223Z" fill="#4cb748"/>
      <path d="M0 40 Q112 0 224 40 L224 223 L0 223Z" fill="#fff"/>
      <path d="M0 45 Q112 8 224 45 L224 223 L0 223Z" fill="url(#gardenTone)" role="img" aria-label="Photo: a woman and an older man picking berries in a garden with a basket"/>
    </svg>
  </div>

  <div class="panel contact">
    <div class="abs brand" style="top:18px">
      <div class="brand__name">MAAS</div>
      <div class="brand__sub">MEADOWLARK AND ALLIED SERVICES, INC.</div>
    </div>
    <p class="abs contact__intro">To learn more about Smart Giving Options and how they can benefit you and Meadowlark and Allied Services, please reach out to our team. We're here to help you navigate these giving methods and answer any question you may have.</p>
    <div class="abs quote">
      <p>Being kind to others is a way of being<br>good to yourself.</p>
      <b>Miriam Holt</b>
    </div>
    <svg class="abs quote__mark" viewBox="0 0 24 16"><circle cx="7" cy="10" r="5" fill="#fff"/><path d="M3 9 Q4 2 10 1" stroke="#fff" stroke-width="2.4" fill="none"/><circle cx="17" cy="10" r="5" fill="#fff"/><path d="M13 9 Q14 2 20 1" stroke="#fff" stroke-width="2.4" fill="none"/></svg>
    <div class="abs will">
      <div class="will__a">If you do not have a will</div>
      <div class="will__b">go to www.WillStarter.org</div>
      <div class="will__c">In 20 minutes you can have a</div>
      <div class="will__d">legal will – for free.</div>
    </div>
    <div class="abs pill-navy">CONTACT US</div>
    <div class="abs question">
      <h3>Have more question?</h3>
      <p>Please contact us at Meadowlark and<br>Allied Services</p>
    </div>
    <div class="abs rows">
      <div class="row"><svg width="20" height="20" viewBox="0 0 20 20"><circle cx="10" cy="10" r="9" fill="none" stroke="#fff" stroke-width=".9"/><path d="M10 15s-3.5-3.6-3.5-6a3.5 3.5 0 017 0c0 2.4-3.5 6-3.5 6z" fill="none" stroke="#fff" stroke-width=".9"/><circle cx="10" cy="9" r="1.2" fill="none" stroke="#fff" stroke-width=".8"/></svg><span>1420 Prairie View Rd. Suite 2<br>Fairhaven, ND 58000</span></div>
      <div class="row"><svg width="20" height="20" viewBox="0 0 20 20"><circle cx="10" cy="10" r="9" fill="none" stroke="#fff" stroke-width=".9"/><rect x="7" y="5" width="6" height="10" rx="1" fill="none" stroke="#fff" stroke-width=".9"/><line x1="9" y1="13.3" x2="11" y2="13.3" stroke="#fff" stroke-width=".8"/></svg><span>Call us Today!<br><b>555-014-2200</b> (ext. 100)</span></div>
      <div class="row"><svg width="20" height="20" viewBox="0 0 20 20"><circle cx="10" cy="10" r="9" fill="none" stroke="#fff" stroke-width=".9"/><circle cx="10" cy="10" r="4.5" fill="none" stroke="#fff" stroke-width=".8"/><ellipse cx="10" cy="10" rx="2" ry="4.5" fill="none" stroke="#fff" stroke-width=".7"/><line x1="5.5" y1="10" x2="14.5" y2="10" stroke="#fff" stroke-width=".7"/></svg><span>jmarlow@meadowlarkallied.org<br><b>www.meadowlarkallied.org</b></span></div>
    </div>
    <div class="abs follow">Follow us&nbsp;<span class="dot" style="background:#2f5fb3"></span><span class="dot" style="background:#d1457f"></span></div>
    <p class="abs disclaimer">This material is for general information only and is not intended to give tax, accounting or legal advice. Meadowlark and Allied Services is not a fiduciary. Please speak with your own tax or financial advisor before making any decision about Smart Giving.</p>
  </div>

  <div class="panel cover">
    <svg class="abs" style="left:0;top:0" width="224" height="523" viewBox="0 0 224 523">
      <defs><linearGradient id="cityTone" x1="0" y1="0" x2="0" y2="1"><stop offset="0" stop-color="#a7a9ae"/><stop offset=".5" stop-color="#9aa4b4"/><stop offset="1" stop-color="#6f83a8"/></linearGradient></defs>
      <rect width="224" height="523" fill="#2b2a72"/>
      <path d="M0 0H224V170 Q112 230 0 170Z" fill="url(#cityTone)" role="img" aria-label="Photo: smiling young woman in glasses and a blue shirt holding a phone on a city street"/>
      <path d="M0 170 Q112 230 224 170 L224 178 Q112 212 0 178Z" fill="#4cb748"/>
      <path d="M0 430 Q112 360 224 400 L224 523 L0 523Z" fill="#4cb748"/>
      <path d="M0 440 Q112 380 224 410 L224 523 L0 523Z" fill="#fff"/>
    </svg>
    <h1 class="abs cover__title">TRANSFORM<span>YOUR GIVING</span></h1>
    <div class="abs cover__tag">
      <svg width="12" height="12" viewBox="0 0 10 10"><circle cx="5" cy="5" r="4.3" fill="none" stroke="#4cb748" stroke-width=".8"/><path d="M3 5l1.5 1.5L7.3 3.6" fill="none" stroke="#4cb748" stroke-width=".9"/></svg>Be Strategic
      <svg width="12" height="12" viewBox="0 0 10 10"><circle cx="5" cy="5" r="4.3" fill="none" stroke="#4cb748" stroke-width=".8"/><path d="M3 5l1.5 1.5L7.3 3.6" fill="none" stroke="#4cb748" stroke-width=".9"/></svg>Be Smart
    </div>
    <p class="abs cover__lead">Discover the impact of Smart Giving with<br>Meadowlark and Allied Services</p>
    <div class="abs cover__icons">
      <div class="ico"><svg width="26" height="26" viewBox="0 0 26 26" fill="none" stroke="#4cb748" stroke-width="1"><circle cx="13" cy="13" r="12"/><circle cx="13" cy="13" r="8"/><circle cx="13" cy="13" r="3"/></svg>Crypto</div>
      <div class="ico"><svg width="26" height="26" viewBox="0 0 26 26" fill="none" stroke="#4cb748" stroke-width="1"><path d="M2 9L13 2l11 7z"/><rect x="3" y="9" width="20" height="2"/><path d="M6 11v10M10 11v10M16 11v10M20 11v10"/><rect x="2" y="21" width="22" height="3"/></svg>DAF's</div>
      <div class="ico"><svg width="28" height="26" viewBox="0 0 28 26" fill="none" stroke="#4cb748" stroke-width="1"><rect x="2" y="15" width="4" height="10"/><rect x="8" y="11" width="4" height="14"/><rect x="14" y="14" width="4" height="11"/><rect x="20" y="7" width="4" height="18"/><path d="M3 11l7-6 6 4 9-7"/></svg>Stocks<br>&amp; Securities</div>
      <div class="ico"><svg width="26" height="26" viewBox="0 0 26 26" fill="none" stroke="#4cb748" stroke-width="1"><rect x="4" y="12" width="18" height="12"/><rect x="2" y="8" width="22" height="4"/><path d="M13 8v16M13 8c-3-6-8-5-6-1M13 8c3-6 8-5 6-1"/></svg>QCDs</div>
      <div class="ico"><svg width="26" height="26" viewBox="0 0 26 26" fill="none" stroke="#4cb748" stroke-width="1"><circle cx="11" cy="12" r="9"/><path d="M11 6v6l3 2M9 1h4"/><circle cx="20" cy="20" r="5"/><path d="M20 17v6"/></svg>Charitable<br>Annuity</div>
    </div>
    <div class="abs brand cover__brand">
      <div class="brand__name">MAAS</div>
      <div class="brand__sub">MEADOWLARK AND ALLIED SERVICES, INC.</div>
    </div>
  </div>
</section>

<!-- INSIDE -->
<section class="sheet sheet--inside">
  <div class="abs inside-mid"></div>
  <svg class="abs hero" viewBox="0 0 675 170">
    <defs><linearGradient id="driveTone" x1="0" y1="0" x2="1" y2="0"><stop offset="0" stop-color="#3a2519"/><stop offset=".45" stop-color="#b5773f"/><stop offset="1" stop-color="#5a4a44"/></linearGradient></defs>
    <path d="M22 0H675V38 Q420 165 200 130 Q80 105 22 0Z" fill="url(#driveTone)" role="img" aria-label="Photo: smiling older couple in sunglasses driving a convertible car at sunset"/>
    <path d="M200 122 Q420 170 675 38 L675 48 Q440 170 215 135Z" fill="#4cb748"/>
  </svg>
  <div class="abs bubble">
    <svg class="abs" style="left:54px;top:76px" width="18" height="12" viewBox="0 0 18 12"><path d="M0 0H18L6 12Z" fill="#2b2a72"/></svg>
    <div class="abs bubble__num">5</div>
    <div class="abs bubble__text">STRATEGIC<br>AND SMART<br>WAYS</div>
  </div>

  <!-- stocks -->
  <div class="way__icon" style="left:19px;top:166px"><svg width="38" height="34" viewBox="0 0 28 26" fill="none" stroke="#fff" stroke-width="1"><rect x="2" y="15" width="4" height="10"/><rect x="8" y="11" width="4" height="14"/><rect x="14" y="14" width="4" height="11"/><rect x="20" y="7" width="4" height="18"/><path d="M3 11l7-6 6 4 9-7"/></svg></div>
  <h3 class="way__title" style="left:93px;top:169px;width:125px">Gifts of Stocks or Appreciated Assets Strategic &amp; Smart</h3>
  <p class="way__hint" style="left:93px;top:212px;width:115px">Consider your long-term publicly traded stock as a way to give to your favorite charity.</p>
  <p class="way__body" style="left:19px;top:240px;width:196px">You can make a significantly bigger impact when you donate long-term appreciated securities, including stock, mutual funds, and bonds, directly to your favorite charity.</p>
  <span class="how" style="left:19px;top:265px">How Does It Work?</span>
  <p class="way__body" style="left:19px;top:280px;width:196px">When you donate stock to a charity, you will generally take a tax deduction for the full market value. Because you are donating stock, your contribution and tax deduction may be significantly higher than contributing the after-tax proceeds. The same benefits apply when you donate mutual funds or bonds.</p>

  <!-- DAF -->
  <div class="way__icon" style="left:19px;top:336px"><svg width="34" height="34" viewBox="0 0 26 26" fill="none" stroke="#fff" stroke-width="1"><path d="M2 9L13 2l11 7z"/><rect x="3" y="9" width="20" height="2"/><path d="M6 11v10M10 11v10M16 11v10M20 11v10"/><rect x="2" y="21" width="22" height="3"/></svg></div>
  <h3 class="way__title" style="left:93px;top:335px;width:120px">Donor-Advised Fund (DAF) Strategic &amp; Smart</h3>
  <p class="way__hint" style="left:93px;top:379px;width:120px">Consider a DAF – a simple, flexible, and tax-advantageous way to give to your favorite charities.</p>
  <p class="way__body" style="left:19px;top:408px;width:196px">A Donor-Advised Fund (DAF), is like a charitable investment account for the sole purpose of supporting your favorite charities.</p>
  <span class="how" style="left:19px;top:430px">How Does It Work?</span>
  <p class="way__body" style="left:19px;top:446px;width:196px">You establish a DAF and contribute cash, stocks, or non-publicly traded assets, cryptocurrency, and private company stock to be eligible for an immediate tax deduction. Those funds are contributed for tax-free growth. You can recommend grants be made from your DAF to any IRS qualified public charity.</p>

  <!-- crypto -->
  <div class="way__icon" style="left:239px;top:176px"><svg width="38" height="38" viewBox="0 0 26 26" fill="none" stroke="#fff" stroke-width="1"><circle cx="13" cy="13" r="12"/><circle cx="13" cy="13" r="8"/><circle cx="13" cy="13" r="3"/></svg></div>
  <h3 class="way__title" style="left:313px;top:188px;width:125px">Cryptocurrency Strategic &amp; Smart</h3>
  <p class="way__hint" style="left:313px;top:219px;width:125px">Consider donating Bitcoin and other cryptocurrencies to your favorite charity.</p>
  <p class="way__body" style="left:240px;top:247px;width:196px">Bitcoin and other cryptocurrencies can be donated to charity just like other appreciated assets such as stocks and other business interests. Before you sell bitcoin and donate the after-tax proceeds, consider donating your bitcoin directly to a favorite charity.</p>
  <span class="how" style="left:240px;top:288px">How Does It Work?</span>
  <p class="way__body" style="left:240px;top:304px;width:196px">Many donors find it useful to open a Donor-Advised Fund (DAF). This strategy includes two significant benefits, both for you and your favorite charity.</p>
  <div class="way__body tick" style="left:240px;top:335px;width:190px"><svg width="10" height="10" viewBox="0 0 10 10"><circle cx="5" cy="5" r="4.3" fill="none" stroke="#4cb748" stroke-width=".8"/><path d="M3 5l1.5 1.5L7.3 3.6" fill="none" stroke="#4cb748" stroke-width=".9"/></svg><span>Your tax deduction will be equal to the fair market value of the donated bitcoin (as determined by a qualified appraisal).</span></div>
  <div class="way__body tick" style="left:240px;top:357px;width:190px"><svg width="10" height="10" viewBox="0 0 10 10"><circle cx="5" cy="5" r="4.3" fill="none" stroke="#4cb748" stroke-width=".8"/><path d="M3 5l1.5 1.5L7.3 3.6" fill="none" stroke="#4cb748" stroke-width=".9"/></svg><span>Your cryptocurrency donation is tax-smart because it may eliminate capital gains taxes on the value / appreciation AND your favorite charity will receive 100% of the value of the contribution.</span></div>
  <p class="way__body" style="left:240px;top:390px;width:196px">Often charities are not able to accept direct donations of bitcoin/crypto so using a DAF is a great way to donate these assets.</p>

  <div class="abs inside-brand">
    <svg class="abs" style="left:0;top:0" width="222" height="107" viewBox="0 0 222 107"><path d="M0 40 Q111 -20 222 40 L222 107 L0 107Z" fill="#4cb748"/><path d="M0 42 Q111 -8 222 42 L222 107 L0 107Z" fill="#fff"/></svg>
    <div class="abs brand">
      <div class="brand__name">MAAS</div>
      <div class="brand__sub">MEADOWLARK AND ALLIED SERVICES, INC.</div>
    </div>
  </div>

  <!-- QCD -->
  <div class="way__icon" style="left:460px;top:138px"><svg width="36" height="36" viewBox="0 0 26 26" fill="none" stroke="#fff" stroke-width="1"><rect x="4" y="12" width="18" height="12"/><rect x="2" y="8" width="22" height="4"/><path d="M13 8v16M13 8c-3-6-8-5-6-1M13 8c3-6 8-5 6-1"/></svg></div>
  <h3 class="way__title" style="left:534px;top:150px;width:135px">Qualified Charitable Distributions (QCDs) Strategic &amp; Smart</h3>
  <p class="way__hint" style="left:534px;top:193px;width:125px">Consider a QCD – when planning your IRA withdrawal strategy…and donate to your favorite charity.</p>
  <p class="way__body" style="left:460px;top:219px;width:205px">IRA owners at age 70 ½ or over can transfer dollars from their IRA to charity tax-free each year. These transfers known as Qualified Charitable Distributions (QCDs) offer eligible older Americans a great way to easily give to charity.</p>
  <span class="how" style="left:460px;top:256px">How Does It Work?</span>
  <p class="way__body" style="left:460px;top:272px;width:205px">Are you 72 and required to take a minimum distribution (RMD) from your IRA but do not need the funds? Consider a Qualified Charitable Distribution. Normally, distributions from a traditional IRA are taxable when received. With a QCD, these distributions become tax-free when paid directly from the IRA to your favorite eligible charity. An IRA owner wishing to make a QCD should contact their IRA trustee, allowing time to complete the transaction before the end of the year to receive the tax benefit.</p>

  <!-- annuity -->
  <div class="way__icon" style="left:460px;top:340px"><svg width="38" height="38" viewBox="0 0 26 26" fill="none" stroke="#fff" stroke-width="1"><circle cx="11" cy="12" r="9"/><path d="M11 6v6l3 2M9 1h4"/><circle cx="20" cy="20" r="5"/><path d="M20 17v6"/></svg></div>
  <h3 class="way__title" style="left:534px;top:352px;width:135px">Charitable Gift Annuity Strategic &amp; Smart</h3>
  <p class="way__hint" style="left:534px;top:382px;width:110px">Consider establishing a Charitable Gift Annuity</p>
  <p class="way__body" style="left:460px;top:411px;width:205px">You make a donation to a single charity. The gift is set aside in a reserve account and invested.</p>
  <span class="how" style="left:460px;top:434px">How Does It Work?</span>
  <p class="way__body" style="left:460px;top:450px;width:205px">A charitable gift annuity is a contract between a donor and a charity. As a donor, you make a sizable gift to charity using cash, securities, or possibly other assets. This money is then invested. In return, you become eligible to take a partial tax deduction for your donation, plus you receive a fixed stream of income from the charity for the rest of your life. At the end of your life (as well as your spouse's, if you're giving as a couple), the charity receives the remainder of the gift.</p>
</section>

</body>
</html>
```